Birchline Septic Solutions

Would like to see some single sided ones but would also like to see some double sided with one sided only being the logo. Owners name is Colin Vandro. Phone number is 555-214-0387
Services are pumping, inspections, installs, and repairs

Contact Information for Business Card

555-241-0387 Colin Vandro Millbrook, OR

```html
<!DOCTYPE html>
<html lang="en">
<head>
<meta charset="utf-8">
<title>Birchline Septic Solutions – Business Card</title>
<link rel="stylesheet" href="https://fonts.googleapis.com/css2?family=Montserrat:wght@600;700&display=swap">
<style>
  :root {
    --page-bg: #e9e6e1;
    --card-top: #f4f5f4;
    --card-bottom: #e3e6e5;
    --card-edge: #d6d9d8;
    --teal-light: #2fc4bd;
    --teal-deep: #128577;
    --swoosh: #1b1c1d;
    --ink: #1f2323;
    --champagne: #f1e3d3;
    --champagne-soft: #e9d6c6;
  }
  html, body {
    margin: 0;
    padding: 0;
    width: 1200px;
    height: 897px;
    overflow: hidden;
    background: var(--page-bg);
  }
  .canvas {
    position: relative;
    width: 1200px;
    height: 897px;
  }
  .business-card {
    position: absolute;
    left: 100px;
    top: 175px;
    width: 1000px;
    height: 546px;
    border-radius: 26px;
    overflow: hidden;
    background: linear-gradient(160deg, var(--card-top), var(--card-bottom));
    box-shadow: 0 0 0 1px var(--card-edge), 0 18px 40px rgba(0,0,0,0.12);
    font-family: "Montserrat", sans-serif;
  }
  .card-graphics {
    position: absolute;
    inset: 0;
  }
  .brand-name {
    position: absolute;
    left: 593px;
    top: 96px;
    width: 400px;
    text-align: center;
    color: var(--ink);
    font-weight: 700;
    line-height: 1;
  }
  .brand-name .brand-main {
    display: block;
    font-size: 60px;
    letter-spacing: 1px;
  }
  .brand-name .brand-sub {
    display: block;
    margin-top: 18px;
    font-size: 19px;
    letter-spacing: 5px;
  }
  .contact {
    position: absolute;
    left: 47px;
    top: 322px;
    color: var(--champagne);
    font-weight: 600;
  }
  .contact-name {
    margin: 0;
    font-size: 54px;
    font-weight: 700;
    letter-spacing: 1px;
    line-height: 1;
  }
  .contact-city {
    margin: 12px 0 0;
    font-size: 29px;
    color: var(--champagne-soft);
    line-height: 1;
  }
  .contact-phone {
    margin: 30px 0 0;
    display: flex;
    align-items: center;
    gap: 14px;
    font-size: 44px;
    color: var(--champagne-soft);
    line-height: 1;
  }
  .phone-icon {
    width: 34px;
    height: 28px;
  }
</style>
</head>
<body>
<div class="canvas">
  <div class="business-card">
    <svg class="card-graphics" width="1000" height="546" viewBox="0 0 1000 546" aria-hidden="true">
      <defs>
        <linearGradient id="tealBand" x1="0" y1="0" x2="0.4" y2="1">
          <stop offset="0" stop-color="#2fc4bd"/>
          <stop offset="1" stop-color="#128577"/>
        </linearGradient>
      </defs>
      <path class="teal-wave" fill="url(#tealBand)"
        d="M0,240 C60,215 110,203 160,203 C300,203 390,262 530,345 C680,432 820,478 1000,432 L1000,546 L0,546 Z"/>
      <path class="black-swoosh" fill="#1b1c1d"
        d="M345,240 C490,292 620,392 760,436 C860,462 950,440 1000,392 L1000,418 C940,468 850,482 750,462 C610,424 480,310 345,240 Z"/>
    </svg>

    <div class="brand-name">
      <span class="brand-main">BIRCHLINE</span>
      <span class="brand-sub">SEPTIC SOLUTIONS</span>
    </div>

    <div class="contact">
      <p class="contact-name">COLIN VANDRO</p>
      <p class="contact-city">Millbrook, OR</p>
      <p class="contact-phone">
        <svg class="phone-icon" viewBox="0 0 34 28" aria-hidden="true">
          <path fill="currentColor" d="M2,10 C2,3 32,3 32,10 L32,13 L25,13 L25,9 L9,9 L9,13 L2,13 Z"/>
          <path fill="currentColor" d="M7,14 L12,11 L22,11 L27,14 L30,26 L4,26 Z"/>
          <circle cx="17" cy="19" r="3.5" fill="#128577"/>
        </svg>
        <span>555-241-0387</span>
      </p>
    </div>
  </div>
</div>
</body>
</html>
```